Website Design for a flight comparison website kestrel fares

m looking to build a flight quote website

The fields of the website should be

THE SITE WILL BE CALLED KESTREL FARES.

WHY USE KESTREL FARES

Widest choice of airfares on sale in the UK
Speak to an expert and take the stress out of
trawling the internet
Save your time and we will search for you
Our lowest airfare guarantee or fly for free
Let us customise the deal if you need flexibility

Ticket Type: Return / One Way

Class: Economy / Premium Economy / Business / First
From: AIRPORTS
To: AIRPORTS

Depart Date: dd/mm/yyyy
Return Date: dd/mm/yyyy

Adults:
Children:
Infants (under 2)

— NEXT PAGE—

-----------------------------------------------
Details of Lead Passenger

First Name:
Middle Name:
Surname:

DOB:

Address 1
Address 2
Town
County
Postcode

Email Adress:
Landline:
Mobile:
—————————————————————————

— NET PAGE —
Your Card Will Not Be Charged

Credit Card

16 digit
EXPIRY
CCV

DEBIT CARD
16 DIGIT
EXPIRY
CCV

SORT CODE
ACCOUNT NUMBER

—SUBMIT—

Thank you for using Kestrel Fares.

Nothing needs to be too complicated just a one page website where users register their interest and then we will call them back offline.

Target Market(s)

People planning to travel last minute to all destinations worldwide.

Industry/Entity Type

Business

Requirements
Must have
• Be cool looking easy user interface.
Nice to have
• Parallax would be nice to make the site look modern and inline with todays websites.

```html
<!DOCTYPE html>
<html lang="en">
<head>
<meta charset="utf-8">
<title>Kestrel Fares – Details of Lead Passenger</title>
<link href="https://fonts.googleapis.com/css2?family=Lato:wght@400;700&display=swap" rel="stylesheet">
<style>
  :root {
    --navy: #2d3e50;
    --amber: #fdb515;
    --green: #9acd3f;
    --field: #f4f4f4;
    --label: #555d66;
    --heading: #2b2f33;
    --hint: #a8adb2;
    --rule: #ececec;
    --footer: #f2f2f2;
    --white: #ffffff;
  }
  * { box-sizing: border-box; margin: 0; padding: 0; }
  html, body { width: 1200px; height: 905px; overflow: hidden; }
  body { font-family: 'Lato', sans-serif; position: relative; background: var(--white); }

  .site-header { position: absolute; left: 0; top: 0; width: 1200px; height: 82px; background: var(--navy); }
  .brand { position: absolute; display: flex; align-items: center; gap: 8px; font-weight: 700; font-size: 24px; }
  .brand-dot { width: 22px; height: 22px; border-radius: 50%; background: var(--amber); }
  .site-header .brand { left: 92px; top: 24px; color: var(--white); }
  .main-nav a { position: absolute; top: 36px; font-size: 11px; font-weight: 700; color: #aebccb; text-decoration: none; letter-spacing: .2px; }
  .main-nav a.active { color: var(--white); }
  .social { position: absolute; top: 36px; width: 11px; height: 11px; border-radius: 50%; background: #aebccb; }

  .hero { position: absolute; left: 0; top: 82px; width: 1200px; height: 772px;
    background: linear-gradient(180deg, #1f9ad8 0%, #4cb3e6 45%, #a9d6ea 72%, #dce9ee 100%); }

  .card { position: absolute; left: 92px; top: 118px; width: 524px; height: 637px; background: var(--white); }
  .card-head { position: absolute; left: 0; top: 0; width: 524px; height: 70px; background: var(--amber); color: var(--white); padding: 14px 0 0 22px; }
  .card-head h1 { font-size: 19px; font-weight: 700; }
  .card-head p { font-size: 11px; margin-top: 2px; }
  .card-head svg { position: absolute; right: 21px; top: 26px; }

  .section-title { position: absolute; font-size: 13px; color: var(--heading); }
  .label { position: absolute; font-size: 9px; color: var(--label); text-transform: uppercase; }
  .field { position: absolute; background: var(--field); font-size: 10.5px; color: var(--hint); padding: 0 13px; display: flex; align-items: center; }
  .field.area { align-items: flex-start; padding-top: 10px; }
  .field.value { color: var(--heading); }
  .field .toggle { position: absolute; right: 0; top: 0; bottom: 0; width: 21px; background: var(--amber); display: flex; align-items: center; justify-content: center; }
  .toggle i { display: block; width: 5px; height: 3px; border-top: 1px solid #fff; border-bottom: 1px solid #fff; }
  .rule { position: absolute; left: 23px; width: 481px; height: 1px; background: var(--rule); }
  .next { position: absolute; left: 23px; top: 579px; width: 480px; height: 29px; background: var(--green); color: var(--white); font-size: 11px; font-weight: 700; display: flex; align-items: center; justify-content: center; }

  .site-footer { position: absolute; left: 0; top: 854px; width: 1200px; height: 51px; background: var(--footer); }
  .site-footer .brand { left: 92px; top: 12px; color: var(--navy); }
  .footer-links { position: absolute; right: 133px; top: 19px; font-size: 12.5px; color: #5b6670; }
  .to-top { position: absolute; left: 1084px; top: 16px; width: 26px; height: 26px; border: 1px solid #2a8fd1; border-radius: 50%; display: flex; align-items: center; justify-content: center; }
</style>
</head>
<body>
  <header class="site-header">
    <div class="brand"><span class="brand-dot"></span>Kestrel Fares</div>
    <nav class="main-nav">
      <a class="active" style="left:464px">HOME</a>
      <a style="left:534px">FLIGHT SEARCH</a>
      <a style="left:655px">ABOUT US</a>
      <a style="left:747px">CONTACT US</a>
      <a style="left:851px">LOGIN</a>
      <a style="left:923px">SIGN UP</a>
    </nav>
    <span class="social" style="left:994px"></span>
    <span class="social" style="left:1025px"></span>
    <span class="social" style="left:1056px"></span>
    <span class="social" style="left:1088px"></span>
  </header>

  <div class="hero" role="img" aria-label="Sky and tropical sea backdrop with a saluting flight attendant, a small island and a jet airliner"></div>

  <form class="card">
    <div class="card-head">
      <h1>Details of Lead Passenger</h1>
      <p>We're bringing you a new level of comfort.</p>
      <svg width="42" height="20" viewBox="0 0 42 20"><path d="M2 17 L40 3 M14 12 L20 4 M18 12 L12 19" stroke="#fff" stroke-width="3" stroke-linecap="round" fill="none"/></svg>
    </div>

    <div class="section-title" style="left:23px;top:94px">Lead Passenger Details</div>
    <div class="label" style="left:23px;top:120px">First name</div>
    <div class="field" style="left:23px;top:133px;width:230px;height:30px">enter first name</div>
    <div class="label" style="left:271px;top:120px">Middle name:</div>
    <div class="field" style="left:271px;top:133px;width:232px;height:30px">enter middle name</div>
    <div class="label" style="left:23px;top:173px">Last name</div>
    <div class="field" style="left:23px;top:186px;width:230px;height:30px">enter last name</div>
    <div class="label" style="left:270px;top:172px">Date of birth</div>
    <div class="field" style="left:270px;top:186px;width:233px;height:30px">select date
      <span class="toggle" style="width:26px"><svg width="12" height="11" viewBox="0 0 12 11"><rect x="1" y="2" width="10" height="8" fill="none" stroke="#fff" stroke-width="1.4"/><path d="M1 4.5h10M3.5 0v3M8.5 0v3" stroke="#fff" stroke-width="1.4"/></svg></span></div>

    <div class="rule" style="top:234px"></div>

    <div class="section-title" style="left:24px;top:256px">Contact Details</div>
    <div class="label" style="left:24px;top:283px">Address 1</div>
    <div class="field area" style="left:24px;top:296px;width:231px;height:76px">enter address</div>
    <div class="label" style="left:272px;top:283px">Address 2</div>
    <div class="field area" style="left:272px;top:296px;width:232px;height:76px">enter address</div>

    <div class="label" style="left:23px;top:383px">Town</div>
    <div class="field" style="left:23px;top:396px;width:108px;height:29px;padding-left:9px">enter town<span class="toggle"><i></i></span></div>
    <div class="label" style="left:148px;top:383px">Country</div>
    <div class="field value" style="left:148px;top:396px;width:106px;height:29px;padding-left:7px">select country<span class="toggle"><i></i></span></div>
    <div class="label" style="left:271px;top:383px">Postcode</div>
    <div class="field" style="left:271px;top:396px;width:108px;height:29px;padding-left:11px">enter postcode<span class="toggle"><i></i></span></div>

    <div class="label" style="left:24px;top:441px">Email address</div>
    <div class="field" style="left:24px;top:454px;width:231px;height:30px">enter email address</div>

    <div class="label" style="left:24px;top:498px">Country code</div>
    <div class="field value" style="left:24px;top:511px;width:107px;height:30px;padding-left:9px">01<span class="toggle"><i></i></span></div>
    <div class="label" style="left:149px;top:498px">Landline</div>
    <div class="field" style="left:149px;top:511px;width:106px;height:30px">landline no.</div>
    <div class="label" style="left:273px;top:498px">Mobile</div>
    <div class="field" style="left:273px;top:511px;width:155px;height:30px">mobile no.</div>

    <div class="rule" style="top:558px"></div>
    <div class="next">NEXT</div>
  </form>

  <footer class="site-footer">
    <div class="brand"><span class="brand-dot"></span>Kestrel Fares</div>
    <div class="footer-links">Home | About | Privacy Policy | Term of Use | © 2014 Kestrel Fares</div>
    <div class="to-top"><svg width="8" height="10" viewBox="0 0 8 10"><path d="M4 9V1M1 4l3-3 3 3" stroke="#2b2f33" stroke-width="1.3" fill="none"/></svg></div>
  </footer>
</body>
</html>
```